Dietitian needs awesome business card

I need a contemporary design that's eye catching but professional.
My card is to given to doctors, specialists and patients alike.
I manage patients with chronic diseases
I have uploaded my logo and current business card, I would also like the other Certified Clinical Nutritionist logo incorporated into the design

Target Market(s)

Doctors, specialists and patients

Industry/Entity Type

Healthcare

Contact Information for Business Card

www.brightfieldnutrition.com.au
Ph: 0427 561 903
Fax: 6457 2183
email: marcus.k.diet@fernmail.com
Space on the back of the card with: Appointment date, Appointment time and appointment location

Font styles to use
Serif

Colors
fbee3e
876aae
ffc214

Requirements
Must have
• My Logo
• Certified Clinical Nutritionist Logo
• My 4 locations - Pinebrook Medical Centre, North Corrin Health, Hollis Medical, Ashcombe Doctors Surgery
Nice to have
• I like the colours in my current business card

```html
<!DOCTYPE html>
<html lang="en">
<head>
<meta charset="utf-8">
<title>Brightfield Nutrition &amp; Dietetics – Business Card</title>
<link rel="stylesheet" href="https://fonts.googleapis.com/css2?family=Lora:ital,wght@0,400;0,600;0,700;1,600;1,700&display=swap">
<style>
  :root {
    --page-bg: #e9e6e1;
    --card-bg: #ffffff;
    --brand-purple: #876aae;
    --brand-purple-deep: #5e4588;
    --brand-yellow: #fbee3e;
    --brand-gold: #ffc214;
    --text-grey: #4a4a4a;
    --rule-purple: #6b5194;
    --badge-gold: #ffc214;
  }
  * { box-sizing: border-box; margin: 0; padding: 0; }
  html, body {
    width: 1200px; height: 900px; overflow: hidden;
    background: var(--page-bg);
    font-family: "Lora", Georgia, serif;
  }
  .card {
    position: absolute;
    width: 600px; height: 340px;
    background: var(--card-bg);
    box-shadow: 0 6px 18px rgba(0,0,0,0.18);
    overflow: hidden;
  }
  .card--front { left: 300px; top: 80px; }
  .card--back  { left: 300px; top: 480px; }

  .corner-mark { position: absolute; left: 0; top: 0; width: 44px; height: 44px; }

  .holder-name {
    position: absolute; left: 62px; top: 24px;
    font-size: 20px; font-weight: 700; color: var(--brand-purple-deep);
  }
  .contact-list {
    position: absolute; left: 48px; top: 100px;
    list-style: none; font-size: 13.5px; color: var(--text-grey);
    line-height: 20px;
  }
  .contact-list li { display: flex; align-items: center; gap: 8px; white-space: nowrap; }
  .contact-icon { width: 11px; height: 11px; flex: none; }
  .holder-title {
    position: absolute; left: 30px; top: 196px;
    font-size: 14.5px; font-style: italic; font-weight: 700; color: var(--brand-purple);
    white-space: nowrap;
  }

  .brand-lockup {
    position: absolute; display: flex; align-items: center; gap: 12px;
  }
  .brand-lockup__dot {
    width: 50px; height: 50px; border-radius: 50%;
    background: var(--brand-purple); flex: none;
  }
  .brand-lockup__name {
    display: flex; flex-direction: column; white-space: nowrap;
    color: var(--brand-purple-deep); font-weight: 600; line-height: 1.05;
  }
  .brand-lockup__main { font-size: 32px; }
  .brand-lockup__sub { font-size: 17px; padding-left: 2px; }
  .card--front .brand-lockup { left: 316px; top: 110px; }
  .card--back .brand-lockup { left: 206px; top: 30px; }

  .front-bands { position: absolute; left: 0; bottom: 0; width: 600px; height: 120px; }
  .badge-panel {
    position: absolute; right: 96px; bottom: 0;
    width: 108px; height: 96px; background: var(--card-bg);
    display: flex; align-items: center; justify-content: center;
  }
  .badge-shape { width: 70px; height: 64px; background: var(--badge-gold); }

  .appointment-form {
    position: absolute; left: 40px; top: 146px; right: 40px;
    display: flex; gap: 14px; font-size: 14px; color: var(--rule-purple);
  }
  .appointment-field { display: flex; align-items: flex-end; gap: 6px; flex: 1; }
  .appointment-field__line { flex: 1; border-bottom: 1px solid var(--rule-purple); height: 16px; }
  .appointment-note {
    position: absolute; left: 40px; top: 196px;
    font-size: 14.5px; font-style: italic; font-weight: 700; color: var(--brand-purple-deep);
  }
  .locations {
    position: absolute; left: 0; right: 0; bottom: 0; height: 74px;
    background: linear-gradient(90deg, var(--brand-yellow), var(--brand-gold));
    display: flex; flex-direction: column; justify-content: center;
    padding: 0 40px; color: var(--brand-purple-deep);
  }
  .locations__label { font-size: 12px; font-weight: 700; letter-spacing: 0.5px; text-transform: uppercase; }
  .locations__list {
    list-style: none; display: flex; flex-wrap: wrap; gap: 2px 18px;
    font-size: 13px; margin-top: 4px;
  }
</style>
</head>
<body>

<section class="card card--front" aria-label="Business card front">
  <svg class="corner-mark" viewBox="0 0 44 44" aria-hidden="true">
    <polygon points="0,44 44,0 44,44" fill="var(--brand-purple)"/>
    <polygon points="0,44 30,14 30,44" fill="var(--brand-purple-deep)" opacity="0.4"/>
  </svg>
  <h1 class="holder-name">Marcus Kellaway</h1>

  <ul class="contact-list">
    <li><svg class="contact-icon" viewBox="0 0 12 12"><path d="M2 1l2 0 1 3-1.5 1a6 6 0 0 0 3 3l1-1.5 3 1 0 2c-5 1-10-4-8.5-8.5z" fill="var(--brand-purple-deep)"/></svg>0427 561 903</li>
    <li><svg class="contact-icon" viewBox="0 0 12 12"><rect x="1" y="3" width="10" height="8" fill="var(--brand-purple-deep)"/><rect x="3" y="1" width="6" height="3" fill="var(--brand-purple-deep)"/></svg>6457 2183</li>
    <li><svg class="contact-icon" viewBox="0 0 12 12"><rect x="1" y="2.5" width="10" height="7" fill="var(--brand-purple-deep)"/><path d="M1 2.5l5 4 5-4" stroke="#fff" fill="none"/></svg>marcus.k.diet@fernmail.com</li>
    <li><svg class="contact-icon" viewBox="0 0 12 12"><circle cx="6" cy="6" r="5" fill="var(--brand-purple-deep)"/></svg>www.brightfieldnutrition.com.au</li>
  </ul>
  <p class="holder-title">Certified Clinical Nutritionist, Nutritionist and Chef</p>

  <div class="brand-lockup">
    <span class="brand-lockup__dot"></span>
    <span class="brand-lockup__name"><span class="brand-lockup__main">Brightfield</span><span class="brand-lockup__sub">Nutrition &amp; Dietetics</span></span>
  </div>

  <svg class="front-bands" viewBox="0 0 600 120" aria-hidden="true">
    <defs>
      <linearGradient id="yellowBand" x1="0" x2="1">
        <stop offset="0" stop-color="var(--brand-gold)"/>
        <stop offset="1" stop-color="var(--brand-yellow)"/>
      </linearGradient>
      <linearGradient id="purpleBand" x1="0" x2="1">
        <stop offset="0" stop-color="var(--brand-purple-deep)"/>
        <stop offset="1" stop-color="var(--brand-purple)"/>
      </linearGradient>
    </defs>
    <polygon points="0,30 250,62 250,92 0,92" fill="url(#yellowBand)"/>
    <polygon points="200,92 250,62 600,104 600,120 0,120 0,92" fill="url(#purpleBand)"/>
  </svg>
  <div class="badge-panel"><div class="badge-shape" role="img" aria-label="Certified clinical nutritionist badge"></div></div>
</section>

<section class="card card--back" aria-label="Business card back">
  <div class="brand-lockup">
    <span class="brand-lockup__dot"></span>
    <span class="brand-lockup__name"><span class="brand-lockup__main">Brightfield</span><span class="brand-lockup__sub">Nutrition &amp; Dietetics</span></span>
  </div>
  <div class="appointment-form">
    <div class="appointment-field">Date:<span class="appointment-field__line"></span></div>
    <div class="appointment-field">Time:<span class="appointment-field__line"></span></div>
    <div class="appointment-field">Location:<span class="appointment-field__line"></span></div>
  </div>
  <p class="appointment-note">If unable to keep appointment, kindly give 24hrs notice.</p>
  <div class="locations">
    <p class="locations__label">Consulting at</p>
    <ul class="locations__list">
      <li>Pinebrook Medical Centre</li>
      <li>North Corrin Health</li>
      <li>Hollis Medical</li>
      <li>Ashcombe Doctors Surgery</li>
    </ul>
  </div>
</section>

</body>
</html>
```